Business Card For Halvenmoor Financial Consulting

Hi, I would like a business card designed. Bold, modern.
Please use the same design as the logo. I have also attached the website design to see the overall theme.
Wordmark Font
Color: Hex: #01AEF7

```html
<!DOCTYPE html>
<html lang="en">
<head>
<meta charset="utf-8">
<title>Halvenmoor Financial Consulting — Business Card</title>
<link rel="stylesheet" href="https://fonts.googleapis.com/css2?family=Lato:wght@400;700;900&display=swap">
<style>
  :root {
    --brand-blue: #01aef7;
    --card-navy: #141f2a;
    --ink-white: #f2f5f7;
    --ink-muted: #c9d2d9;
    --backdrop: #d6d6d6;
    --pattern-dark: #101820;
  }
  * { margin: 0; padding: 0; box-sizing: border-box; }
  html, body {
    width: 1200px; height: 997px; overflow: hidden;
    background: var(--backdrop);
    font-family: "Lato", sans-serif;
  }
  .sheet {
    position: relative; width: 1200px; height: 997px;
    display: flex; align-items: center; justify-content: center; gap: 40px;
  }
  .card {
    position: relative; width: 540px; height: 310px;
    border-radius: 3px; overflow: hidden;
    box-shadow: 0 10px 30px rgba(0,0,0,.18);
  }
  /* Back of card */
  .card-back {
    background: linear-gradient(225deg, var(--pattern-dark) 0%, #0f3550 40%, #0679b0 75%, var(--brand-blue) 100%);
  }
  /* Front of card */
  .card-front { background: var(--card-navy); color: var(--ink-white); }
  .divider-diagonal { position: absolute; inset: 0; }
  .wordmark {
    position: absolute; top: 38px; right: 34px;
    display: flex; align-items: center; gap: 12px;
  }
  .wordmark-square {
    width: 26px; height: 26px; border: 3px solid var(--brand-blue);
  }
  .wordmark-name {
    font-weight: 700; font-size: 19px; letter-spacing: 2px;
    color: var(--ink-white); text-transform: uppercase;
  }
  .person {
    position: absolute; left: 34px; bottom: 30px;
  }
  .person-name {
    font-weight: 900; font-size: 25px; color: var(--brand-blue);
    letter-spacing: .5px; line-height: 1;
  }
  .person-title {
    font-size: 14px; color: var(--ink-white); margin-top: 4px;
  }
  .person-rule {
    width: 150px; height: 1.5px; background: var(--brand-blue); margin: 10px 0 9px;
  }
  .contact-list { list-style: none; }
  .contact-list li {
    display: flex; align-items: center; gap: 8px;
    font-size: 12px; line-height: 17px; color: var(--ink-white);
  }
  .contact-list svg { width: 10px; height: 10px; fill: var(--brand-blue); flex: none; }
  .company {
    position: absolute; right: 34px; bottom: 120px; text-align: right;
    font-size: 12px; line-height: 16px; color: var(--ink-muted);
  }
  .company-name { font-weight: 700; color: var(--ink-white); font-size: 12.5px; }
  .company-web { color: var(--brand-blue); margin-top: 4px; }
</style>
</head>
<body>
<main class="sheet">
  <section class="card card-back" role="img" aria-label="Card back: repeating brand emblem pattern over a blue-to-navy gradient"></section>

  <section class="card card-front">
    <svg class="divider-diagonal" viewBox="0 0 540 310" aria-hidden="true">
      <defs>
        <linearGradient id="rule-fade" x1="0" y1="1" x2="1" y2="0">
          <stop offset="0" stop-color="#01aef7" stop-opacity=".9"/>
          <stop offset="1" stop-color="#01aef7" stop-opacity="0"/>
        </linearGradient>
      </defs>
      <line x1="184" y1="190" x2="440" y2="96" stroke="url(#rule-fade)" stroke-width="1.2"/>
    </svg>

    <div class="wordmark">
      <span class="wordmark-square"></span>
      <span class="wordmark-name">Halvenmoor Consulting</span>
    </div>

    <div class="company">
      <p class="company-name">Halvenmoor Financial Consulting</p>
      <p>Your Address, City</p>
      <p>State, Zip Code 1235</p>
      <p class="company-web">www.HalvenmoorConsulting.com</p>
    </div>

    <div class="person">
      <h1 class="person-name">DANIEL REYES</h1>
      <p class="person-title">Founder &amp; CEO</p>
      <div class="person-rule"></div>
      <ul class="contact-list">
        <li><svg viewBox="0 0 10 10"><path d="M2 0.5h2l0.8 2.4-1.3 0.9a5 5 0 0 0 2.7 2.7l0.9-1.3 2.4 0.8v2A1.5 1.5 0 0 1 8 9.5 7.5 7.5 0 0 1 0.5 2 1.5 1.5 0 0 1 2 0.5z"/></svg>(555) 014-2280</li>
        <li><svg viewBox="0 0 10 10"><path d="M2.5 0h5a1 1 0 0 1 1 1v8a1 1 0 0 1-1 1h-5a1 1 0 0 1-1-1V1a1 1 0 0 1 1-1zm0.5 1.5v6h4v-6z"/></svg>(555) 014-2281</li>
        <li><svg viewBox="0 0 10 10"><path d="M2.5 0h5v3h-5zM0.5 3.5h9v4.5h-2v2h-5v-2h-2zM3.5 6.5v2.5h3V6.5z"/></svg>(555) 014-2282</li>
        <li><svg viewBox="0 0 10 10"><path d="M0 1.5h10v7H0zm1 1v0.4l4 2.6 4-2.6V2.5z"/></svg>info@HalvenmoorConsulting.com</li>
      </ul>
    </div>
  </section>
</main>
</body>
</html>
```